Business Card for a mobile physiotherapy company

I need a layout for a business card for a mobile physiotherapy company.
Slogan is "Mobile Physiotherapy - Your Road To Recovery"
Phone number is 867-555-0142
Email VardenTherapy@postnest.ca (subject to change with website)
Website www.VardenTherapy.ca
My name and credentials: Luke Varden Luke Varden, BSc(kin), MPT, CAFCI, IMS
Information maybe included: Direct Billing, Services including Physiotherapy, IMS, acupuncture
Maybe include facebook and instagram logos
One side with the logo clean and sharp
Other side with details, try not to look too busy, keep everything concise

```html
<!DOCTYPE html>
<html lang="en">
<head>
<meta charset="utf-8">
<title>Varden Therapy – Business Card</title>
<link rel="stylesheet" href="https://fonts.googleapis.com/css2?family=Roboto:ital,wght@0,400;0,500;0,700;1,400&display=swap">
<style>
  :root {
    --navy: #2c4870;
    --forest: #0c5446;
    --paper: #ffffff;
    --ink: #4a4a4a;
    --backdrop: #eceae6;
  }
  * { box-sizing: border-box; margin: 0; padding: 0; }
  html, body {
    width: 1125px; height: 1200px; overflow: hidden;
    background: var(--backdrop);
    font-family: "Roboto", Arial, sans-serif;
  }
  .sheet { position: relative; width: 1125px; height: 1200px; }
  .card {
    position: absolute; left: 162px; width: 800px; height: 457px;
    box-shadow: 0 3px 8px rgba(0,0,0,0.25);
    overflow: hidden;
  }
  .card-front { top: 113px; background: var(--paper); }
  .card-back { top: 630px; background: var(--navy); color: var(--paper); }

  .name-band {
    position: absolute; left: 0; top: 61px; width: 800px; height: 119px;
    background: var(--navy);
  }
  .name-band-accent {
    position: absolute; right: 0; top: 0; width: 185px; height: 119px;
    background: var(--forest);
  }
  .holder { position: absolute; left: 58px; top: 22px; color: var(--paper); }
  .holder-name { font-size: 29px; font-weight: 700; letter-spacing: 0.3px; line-height: 32px; }
  .holder-credentials { font-size: 19px; font-weight: 500; line-height: 22px; }
  .holder-billing { font-size: 20px; font-weight: 500; line-height: 28px; margin-top: 2px; }

  .brand-front {
    position: absolute; left: 470px; top: 200px; width: 280px;
    text-align: center; color: var(--navy); font-weight: 700;
  }
  .brand-front .brand-main { font-size: 58px; letter-spacing: 5px; line-height: 64px; }
  .brand-front .brand-sub { font-size: 27px; letter-spacing: 12px; line-height: 34px; padding-left: 12px; }

  .contacts { position: absolute; left: 58px; top: 328px; list-style: none; }
  .contacts li {
    display: flex; align-items: center; gap: 12px;
    font-size: 19px; color: var(--ink); height: 26px;
  }
  .contacts svg { width: 17px; height: 17px; fill: var(--navy); }

  .social { position: absolute; right: 47px; top: 40px; display: flex; gap: 6px; }
  .social span { width: 37px; height: 37px; border-radius: 50%; background: var(--paper); }

  .brand-back {
    position: absolute; left: 0; top: 150px; width: 800px;
    text-align: center; color: var(--paper); font-weight: 700;
  }
  .brand-back .brand-main { font-size: 72px; letter-spacing: 7px; line-height: 80px; }
  .brand-back .brand-sub { font-size: 32px; letter-spacing: 16px; line-height: 42px; padding-left: 16px; }

  .slogan {
    position: absolute; left: 0; top: 377px; width: 800px; text-align: center;
    font-size: 19px; font-style: italic;
  }
  .services {
    position: absolute; left: 0; top: 405px; width: 800px; text-align: center;
    font-size: 19px;
  }
</style>
</head>
<body>
<main class="sheet">
  <section class="card card-front" aria-label="Card front">
    <div class="name-band">
      <div class="name-band-accent"></div>
      <div class="holder">
        <p class="holder-name">LUKE VARDEN</p>
        <p class="holder-credentials">BSc(kin), MPT, CAFCI, IMS</p>
        <p class="holder-billing">Direct Billing</p>
      </div>
    </div>

    <div class="brand-front">
      <p class="brand-main">VARDEN</p>
      <p class="brand-sub">THERAPY</p>
    </div>

    <ul class="contacts">
      <li>
        <svg viewBox="0 0 24 24" aria-hidden="true"><path d="M6.6 10.8a15.1 15.1 0 0 0 6.6 6.6l2.2-2.2a1 1 0 0 1 1-.25 11.4 11.4 0 0 0 3.6.57 1 1 0 0 1 1 1V20a1 1 0 0 1-1 1A17 17 0 0 1 3 4a1 1 0 0 1 1-1h3.5a1 1 0 0 1 1 1c0 1.25.2 2.45.57 3.57a1 1 0 0 1-.25 1z"/></svg>
        867-555-0142
      </li>
      <li>
        <svg viewBox="0 0 24 24" aria-hidden="true"><path d="M3 6h18v12H3z M4.5 7.5v.4L12 13l7.5-5.1v-.4z" fill-rule="evenodd"/></svg>
        VardenTherapy@postnest.ca
      </li>
      <li>
        <svg viewBox="0 0 24 24" aria-hidden="true"><path d="M12 2a10 10 0 1 0 0 20 10 10 0 0 0 0-20zm-1 17.9A8 8 0 0 1 4.1 10.1L9 15v1a2 2 0 0 0 2 2zm6.9-2.5A2 2 0 0 0 16 16h-1v-3a1 1 0 0 0-1-1H8v-2h2a1 1 0 0 0 1-1V7h2a2 2 0 0 0 2-2v-.4a8 8 0 0 1 2.9 12.8z"/></svg>
        www.VardenTherapy.ca
      </li>
    </ul>
  </section>

  <section class="card card-back" aria-label="Card back">
    <div class="social" aria-label="Social media">
      <span></span><span></span>
    </div>
    <div class="brand-back">
      <p class="brand-main">VARDEN</p>
      <p class="brand-sub">THERAPY</p>
    </div>
    <p class="slogan">Mobile Physiotherapy - Your Road To Recovery</p>
    <p class="services">Physiotherapy • IMS • Acupuncture</p>
  </section>
</main>
</body>
</html>
```